Elegant Business Card for Technology Company

Client is a supplier of innovative industrial communications and automation equipment since 2002. This contest is to gather fresh ideas for a redesign of the existing business card. Client is looking for design that best communicates tagline "Industrial Networking and Computing Specialist".

Design submissions should look modern, clean, elegant and professional. It should not be cluttered. Use white as the primary colour. Orange and black as secondary colour. Refer to jpeg File 1 on the current design.

Fonts used by Client used include Arial Regular, Arial Black, Roboto Regular, Roboto Black and Lato.

The winning design will be sent for offset printing using super white 250gsm artcard paper (open for suggestions).

Target Market(s)

System Engineers, Project Managers, Purchasing Managers from companies providing engineering services for Smart Cities.

Industry/Entity Type

Information Technology

Contact Information for Business Card

Refer to PDF File 3 for Business Card Details. Priority of short contact information would be as follows Name > Job Title > Email > Mobile > Web > Tel > Fax > Business Address >UEN (UEN represents company registration number)

Font styles to use
Sans Serif

Colors
ffffff
f37122
000000
5c5c5c

Requirements
Must have
• Refer to AI File 2 (Company Logo) & PDF File 3 (Information on Namecard)
Should not have
• No QR codes
• No Social Media Icons
• Do not create full Black or Orange colour background

```html
<!DOCTYPE html>
<html lang="en">
<head>
<meta charset="utf-8">
<title>KVR Business Card</title>
<link href="https://fonts.googleapis.com/css2?family=Open+Sans:wght@400;600;700;800&display=swap" rel="stylesheet">
<style>
  :root {
    --backdrop: #3b3532;
    --card: #ffffff;
    --orange: #f37122;
    --ink: #000000;
    --grey: #5c5c5c;
    --rule: #e6e6e6;
  }
  html, body {
    margin: 0;
    padding: 0;
    width: 1200px;
    height: 844px;
    overflow: hidden;
    background: var(--backdrop);
    font-family: "Open Sans", Arial, sans-serif;
  }
  .stage {
    position: relative;
    width: 1200px;
    height: 844px;
  }
  .card {
    position: absolute;
    top: 262px;
    width: 540px;
    height: 320px;
    background: var(--card);
    border-radius: 3px;
    box-sizing: border-box;
    color: var(--ink);
    overflow: hidden;
    box-shadow: 0 10px 24px rgba(0, 0, 0, 0.35);
  }
  .card--front { left: 40px; }
  .card--back { left: 620px; }

  /* front */
  .brand {
    position: absolute;
    left: 40px;
    top: 36px;
    display: flex;
    align-items: center;
    gap: 14px;
  }
  .brand__dot {
    width: 74px;
    height: 74px;
    border-radius: 50%;
    background: var(--orange);
  }
  .brand__name {
    font-size: 50px;
    font-weight: 800;
    line-height: 1;
    color: var(--ink);
    letter-spacing: 1px;
  }
  .brand__company {
    position: absolute;
    left: 128px;
    top: 96px;
    font-size: 14px;
    font-weight: 700;
    color: var(--ink);
  }
  .contacts {
    position: absolute;
    right: 28px;
    top: 104px;
    list-style: none;
    margin: 0;
    padding: 0;
    text-align: right;
    font-size: 14px;
    line-height: 22px;
    color: var(--grey);
  }
  .contacts li {
    display: flex;
    justify-content: flex-end;
    align-items: center;
    gap: 6px;
  }
  .contacts svg { width: 12px; height: 12px; fill: var(--orange); }
  .person {
    position: absolute;
    left: 40px;
    top: 160px;
  }
  .person__name {
    font-size: 21px;
    font-weight: 600;
    color: var(--orange);
    margin: 0;
    line-height: 1.1;
  }
  .person__title {
    font-size: 14px;
    color: var(--grey);
    margin: 0 0 12px;
  }
  .person__uen {
    font-size: 16px;
    color: var(--ink);
    margin: 0 0 10px;
  }
  .person__uen span { color: var(--orange); }
  .person__address {
    font-size: 16px;
    line-height: 24px;
    color: var(--ink);
    margin: 0;
  }
  .edge-band {
    position: absolute;
    left: 0;
    right: 0;
    bottom: 0;
    height: 6px;
    background: var(--orange);
  }

  /* back */
  .back__name {
    position: absolute;
    left: 44px;
    top: 36px;
    font-size: 62px;
    font-weight: 800;
    line-height: 1;
    letter-spacing: 1px;
    color: var(--ink);
  }
  .tagline {
    position: absolute;
    left: 44px;
    top: 112px;
    font-size: 16px;
    font-weight: 600;
    color: var(--orange);
    margin: 0;
  }
  .services {
    position: absolute;
    left: 44px;
    top: 146px;
    margin: 0;
    padding: 0;
    list-style: none;
    font-size: 14px;
    font-weight: 600;
    line-height: 27px;
    color: var(--grey);
  }
  .services li::before {
    content: "";
    display: inline-block;
    width: 9px;
    height: 9px;
    border-radius: 50%;
    background: var(--orange);
    margin-right: 10px;
    vertical-align: 1px;
  }
</style>
</head>
<body>
<main class="stage">
  <section class="card card--front">
    <div class="brand">
      <div class="brand__dot"></div>
      <div class="brand__name">KVR</div>
    </div>
    <div class="brand__company">Korvane Asia Pacific Pte Ltd</div>

    <ul class="contacts">
      <li>+65 8123 4567
        <svg viewBox="0 0 12 12"><rect x="3" y="0" width="6" height="12" rx="1"/></svg></li>
      <li>65 6234 5610
        <svg viewBox="0 0 12 12"><path d="M2 1l3 0 1 3-2 1c1 2 2 3 3 3l1-2 3 1 0 3c-6 0-10-4-9-9z"/></svg></li>
      <li>+ 65 6234 5699
        <svg viewBox="0 0 12 12"><rect x="1" y="4" width="10" height="7" rx="1"/><rect x="3" y="1" width="6" height="3"/></svg></li>
      <li>sales@korvane.com.sg
        <svg viewBox="0 0 12 12"><rect x="0" y="2" width="12" height="8" rx="1"/></svg></li>
      <li>www.korvane.com.sg
        <svg viewBox="0 0 12 12"><circle cx="6" cy="6" r="6"/></svg></li>
    </ul>

    <div class="person">
      <p class="person__name">Daniel Lim</p>
      <p class="person__title">Sales Manager</p>
      <p class="person__uen"><span>UEN No:</span> 200412345K</p>
      <p class="person__address">25 Kallang Way Link Hub #05-12<br>(Lobby B), Singapore 349321</p>
    </div>
    <div class="edge-band"></div>
  </section>

  <section class="card card--back">
    <div class="back__name">KVR</div>
    <p class="tagline">Industrial Networking And Computing Specialist</p>
    <ul class="services">
      <li>Industrial Enthernet / Wireless / Cellular</li>
      <li>Industrial and Embedded Computing</li>
      <li>Serial / Fieldbus Connectivity</li>
      <li>IP Video Surveillance</li>
      <li>Remote Automation</li>
    </ul>
    <div class="edge-band"></div>
  </section>
</main>
</body>
</html>
```